Maple n Brook - Contact/Landing Page

I need a landing page which will essentially be the page that customers will go to from the 'website' link on QTV listing. It will provide a short overview of services which need to be selectable. a little further down can capture some contact details followed by a large Submit Now button etc...

I have some icon/logo's that can be utilised at the bottom of the page as industry type references.

Target Market(s)

End of Lease Cleaning Services

Industry/Entity Type

Cleaning Service

Colors

Designer to choose colors to be used in the design.

Requirements
Must have
• As per description
Should not have
• Colours to match my website maplenbrook.com.au

```html
<!DOCTYPE html>
<html lang="en">
<head>
<meta charset="utf-8">
<title>Maple n Brook – End of Lease Services</title>
<link href="https://fonts.googleapis.com/css2?family=Rubik:wght@500;700&family=Roboto:wght@300;400;500&display=swap" rel="stylesheet">
<style>
  :root {
    --brand-blue: #1479be;
    --band-blue: #0f6fae;
    --ink: #111111;
    --body-text: #555b61;
    --card-bg: #ffffff;
    --section-grey: #f2f3f5;
    --field-border: #d9dde1;
    --placeholder: #6b7075;
    --logo-grey: #c3c6cb;
    --white: #ffffff;
  }
  * { box-sizing: border-box; margin: 0; padding: 0; }
  html, body { width: 833px; height: 1200px; overflow: hidden; }
  body { position: relative; font-family: "Roboto", Arial, sans-serif; background: var(--white); color: var(--ink); }

  .hero { position: absolute; left: 0; top: 0; width: 833px; height: 333px; background: var(--brand-blue); }
  .brand { position: absolute; left: 0; top: 70px; width: 833px; display: flex; flex-direction: column; align-items: center; gap: 14px; }
  .brand-mark { width: 74px; height: 74px; border-radius: 50%; background: var(--logo-grey); }
  .brand-name { font-family: "Rubik", Arial, sans-serif; font-weight: 700; font-size: 30px; color: var(--white); letter-spacing: 1px; }
  .hero-title { position: absolute; left: 0; top: 266px; width: 833px; text-align: center; font-family: "Rubik", Arial, sans-serif; font-weight: 700; font-size: 24px; color: var(--white); }

  .service-card { position: absolute; top: 415px; width: 213px; height: 215px; background: var(--card-bg); box-shadow: 0 1px 6px rgba(0,0,0,0.12); padding: 16px 19px; }
  .service-card.cleaning { left: 77px; }
  .service-card.carpet { left: 311px; }
  .service-card.pest { left: 543px; }
  .service-icon { width: 46px; height: 46px; display: block; }
  .service-title { margin-top: 13px; font-family: "Rubik", Arial, sans-serif; font-weight: 500; font-size: 12.5px; color: var(--ink); }
  .service-rule { width: 24px; height: 2px; background: var(--brand-blue); margin-top: 10px; }
  .service-text { margin-top: 10px; font-size: 9.6px; line-height: 17.8px; color: var(--body-text); font-weight: 400; }
  .service-select { margin-top: 10px; display: flex; align-items: center; gap: 12px; font-family: "Rubik", Arial, sans-serif; font-weight: 500; font-size: 9.5px; color: var(--ink); }
  .service-select input { width: 8px; height: 8px; margin: 0; }

  .partners { position: absolute; left: 0; top: 705px; width: 833px; height: 155px; background: var(--band-blue); }
  .partner-arrow { position: absolute; top: 70px; width: 14px; height: 18px; }
  .partner-arrow.prev { left: 32px; }
  .partner-arrow.next { left: 787px; }
  .partner-badge { position: absolute; top: 51px; height: 54px; border-radius: 3px; }
  .partner-badge.one { left: 76px; width: 154px; background: #c7cde0; top: 57px; height: 42px; }
  .partner-badge.two { left: 264px; width: 126px; background: #1a1a1a; }
  .partner-badge.three { left: 434px; width: 101px; background: #e6edf4; }
  .partner-badge.four { left: 578px; width: 179px; background: #8fb84a; }

  .contact { position: absolute; left: 0; top: 860px; width: 833px; height: 307px; background: var(--section-grey); }
  .contact-title { position: absolute; left: 0; top: 43px; width: 833px; text-align: center; font-family: "Rubik", Arial, sans-serif; font-weight: 700; font-size: 23px; color: var(--ink); }
  .field { position: absolute; background: var(--white); border: 1px solid var(--field-border); border-radius: 2px; font-family: "Roboto", Arial, sans-serif; font-size: 10px; color: var(--placeholder); padding: 0 9px; }
  .field::placeholder { color: var(--placeholder); }
  .field.short { top: 101px; width: 164px; height: 36px; }
  .field.first { left: 80px; }
  .field.last { left: 250px; }
  .field.phone { left: 420px; }
  .field.email { left: 589px; }
  .field.subject { top: 144px; left: 82px; width: 670px; height: 60px; padding-top: 8px; resize: none; }
  .submit-btn { position: absolute; left: 362px; top: 228px; width: 110px; height: 33px; border: none; border-radius: 17px; background: var(--brand-blue); color: var(--white); font-family: "Roboto", Arial, sans-serif; font-weight: 500; font-size: 9.5px; display: flex; align-items: center; justify-content: center; gap: 7px; }

  .footer { position: absolute; left: 0; top: 1167px; width: 833px; height: 33px; background: var(--band-blue); color: var(--white); font-size: 9.8px; text-align: center; line-height: 33px; }
</style>
</head>
<body>
  <header class="hero">
    <div class="brand">
      <span class="brand-mark"></span>
      <span class="brand-name">MAPLE N BROOK</span>
    </div>
    <h1 class="hero-title">END OF LEASE SERVICES</h1>
  </header>

  <article class="service-card cleaning">
    <svg class="service-icon" viewBox="0 0 46 46" fill="none" stroke="#1479be" stroke-width="1.6" stroke-linejoin="round">
      <path d="M14 8h16l6 4v6h-4v-3H22v6h-4v-5h-4z"/>
      <path d="M18 21h6v5l3 4v14H15V30l3-4z"/>
      <rect x="18" y="33" width="6" height="6" rx="1.5"/>
      <path d="M3 6l5 1M2 11h6M3 16l5-1"/>
    </svg>
    <h2 class="service-title">CLEANING</h2>
    <div class="service-rule"></div>
    <p class="service-text">Presenting your property and getting your bond back has never been easier. We make light work of cleaning.</p>
    <label class="service-select">SELECT <input type="checkbox"></label>
  </article>

  <article class="service-card carpet">
    <svg class="service-icon" viewBox="0 0 46 46" fill="none" stroke="#1479be" stroke-width="1.6" stroke-linejoin="round">
      <path d="M22 40V8a5 5 0 0 1 10 0v32"/>
      <path d="M18 42h22"/>
      <path d="M3 40V26a6 6 0 0 1 6-6h4a6 6 0 0 1 6 6v14z"/>
      <path d="M9 20V6h3v14"/>
      <path d="M7 30h8M7 34h8"/>
    </svg>
    <h2 class="service-title">CARPET CLEANING</h2>
    <div class="service-rule"></div>
    <p class="service-text">Our carpet cleaning service is of the highest quality and are undertaken in a multi-stage process done</p>
    <label class="service-select">SELECT <input type="checkbox"></label>
  </article>

  <article class="service-card pest">
    <svg class="service-icon" viewBox="0 0 46 46" fill="none" stroke="#1479be" stroke-width="1.6" stroke-linejoin="round">
      <path d="M4 12V4h8M34 4h8v8M42 34v8h-8M12 42H4v-8"/>
      <ellipse cx="23" cy="25" rx="7" ry="9"/>
      <circle cx="23" cy="14" r="3.5"/>
      <path d="M23 17v17M16 22h-6l-2-3M16 28H9l-2 3M30 22h6l2-3M30 28h7l2 3"/>
    </svg>
    <h2 class="service-title">PEST CONTROL</h2>
    <div class="service-rule"></div>
    <p class="service-text">We are licensed and equipped to offer a full range of pest control services to the residential and commercial</p>
    <label class="service-select">SELECT <input type="checkbox"></label>
  </article>

  <section class="partners" aria-label="Industry partners">
    <svg class="partner-arrow prev" viewBox="0 0 14 18" fill="none" stroke="#ffffff" stroke-width="2.4"><path d="M11 2L4 9l7 7"/></svg>
    <div class="partner-badge one" role="img" aria-label="Partner badge"></div>
    <div class="partner-badge two" role="img" aria-label="Certification badge"></div>
    <div class="partner-badge three" role="img" aria-label="Training partner badge"></div>
    <div class="partner-badge four" role="img" aria-label="College badge"></div>
    <svg class="partner-arrow next" viewBox="0 0 14 18" fill="none" stroke="#ffffff" stroke-width="2.4"><path d="M3 2l7 7-7 7"/></svg>
  </section>

  <section class="contact">
    <h2 class="contact-title">CONTACT US</h2>
    <input class="field short first" type="text" placeholder="First Name">
    <input class="field short last" type="text" placeholder="Sur Name">
    <input class="field short phone" type="text" placeholder="Phone No">
    <input class="field short email" type="text" placeholder="Email">
    <textarea class="field subject" placeholder="Subject"></textarea>
    <button class="submit-btn" type="button">SUBMIT NOW
      <svg width="9" height="9" viewBox="0 0 10 10"><circle cx="5" cy="5" r="5" fill="#ffffff"/><path d="M3 5h4M5 3l2 2-2 2" stroke="#1479be" stroke-width="1.3" fill="none"/></svg>
    </button>
  </section>

  <footer class="footer">© 2021 Maple n Brook. All Rights Reserved</footer>
</body>
</html>
```